Fitness Equipment & Service

I want to make the card eye catching and fun. We are called Corvane Motion Limited and we are based in Wales. We sell, install and service all types of fitness equipment from Skipping ropes, right through the Dumbbells, Kettle bells and Barbells through to state of the art Treadmills, Running Machines and Strength Equipment. We also design and install changing room furniture and lockers.

TYPOGRAPHY
We would like to use Futrura. Futura has an appearance of efficiency and forwardness. The typeface is derived
from simple geometric forms (near-perfect circles, triangles and squares) and is based on strokes of
near-even weight, which are low in contrast. This is most visible in the almost perfectly round stroke of
the o, which is nonetheless slightly ovoid.
The lowercase has tall ascenders, which rise above the cap line. The uppercase
characters present proportions similar to those of classical Roman capitals.

TYPOGRAPHIC CONSIDERATIONS
No Strike though
No Horizontal Scaling
No Drop Shadows
No Effects
Never use less than 120% Leading

OUR CORPORATE COLOURS
BRAND GUIDELINES
We were thinking that our primary colour palette consists of the Acid Green (Pantone 382) and Process Black.

We work closely with tquarly Ltd and would like to include their name on the card somewhere. I have attached images of the other brands that we work with as an idea or the small icons I have included that illustrate what we do?. I have very kindly been given permission to use any of the images off the files that I have included below, so I hope these help. I will include these below. I would be open to suggestions if it made the card more striking Can you do it?
Updates

Hi All, Just wanted to add a few thoughts but you are the guys with the creative visions (thats why are here) We are based in Wales, UK and we would be open to lots of different ideas on a theme but must be eye catching, Bold and FUN. If you can or think that the Welsh or any dragon could be put in there then go for it (its not a must have) We have also added some ideas for colour but again its over to you!! GO FOR IT ! Thanks and look forward to your visions! Owen

Hi All, Just thought I would sen through the contact details that need to be on the card. (if you want to play around with icons instead of the wording twitter, Facebook, go for it): Corvane Motion Limited Owen Pritchard Managing Director Mob: +44 (0)7582 913 406 e-mail: sales@corvanemotion.co.uk Web: Corvanemotion.co.uk twitter: @motionLetterbin Facebook: Corvane Motion Limited

```html
<!DOCTYPE html>
<html lang="en">
<head>
<meta charset="utf-8">
<title>Corvane Motion Limited – Business Card</title>
<link href="https://fonts.googleapis.com/css2?family=Jost:wght@400;600&display=swap" rel="stylesheet">
<style>
  :root {
    --navy: #12285a;
    --wave-blue: #2563ad;
    --title-blue: #1f5fae;
    --card-white: #ffffff;
    --stage: #e9e9ec;
    --mark-blue: #1d3f8a;
  }
  * { margin: 0; padding: 0; box-sizing: border-box; }
  html, body {
    width: 1200px; height: 900px; overflow: hidden;
    background: var(--stage);
    font-family: "Jost", "Futura", sans-serif;
  }
  .business-card {
    position: absolute; left: 150px; top: 172px;
    width: 900px; height: 556px;
    background: var(--card-white);
    overflow: hidden;
  }
  .card-waves { position: absolute; inset: 0; width: 900px; height: 556px; }
  .brand-block { position: absolute; left: 70px; top: 45px; width: 380px; }
  .brand-dot {
    display: block; width: 190px; height: 190px; margin-left: 80px;
    border-radius: 50%; background: var(--mark-blue);
  }
  .brand-name {
    margin-top: 26px;
    font-weight: 600; font-size: 30px; line-height: 1.2;
    color: var(--navy); letter-spacing: 0.5px;
  }
  .person {
    position: absolute; right: 48px; top: 62px; text-align: right;
  }
  .person-name { font-weight: 600; font-size: 30px; line-height: 1.2; color: var(--navy); }
  .person-title { font-weight: 400; font-size: 24px; line-height: 1.3; color: var(--title-blue); }
  .contact-list {
    position: absolute; right: 40px; top: 360px; list-style: none;
  }
  .contact-item {
    display: flex; justify-content: flex-end; align-items: center;
    height: 32.5px; font-size: 24px; line-height: 1.3; color: var(--card-white);
  }
  .contact-icon { width: 20px; height: 20px; margin-left: 16px; flex: none; }
</style>
</head>
<body>
  <main class="business-card">
    <svg class="card-waves" viewBox="0 0 900 556" aria-hidden="true">
      <path fill="var(--wave-blue)" d="M0,307 C100,380 180,430 290,420 C430,405 600,205 740,195 C810,190 870,220 900,245 L900,556 L0,556 Z"/>
      <path fill="var(--card-white)" d="M0,318 C100,391 180,441 290,431 C430,416 600,216 740,206 C810,201 870,231 900,256 L900,556 L0,556 Z"/>
      <path fill="var(--navy)" d="M0,327 C100,400 180,450 290,440 C430,425 600,225 740,215 C810,210 870,240 900,265 L900,556 L0,556 Z"/>
    </svg>

    <div class="brand-block">
      <span class="brand-dot"></span>
      <p class="brand-name">Corvane Motion Limited</p>
    </div>

    <div class="person">
      <p class="person-name">Owen Pritchard</p>
      <p class="person-title">Managing Director</p>
    </div>

    <ul class="contact-list">
      <li class="contact-item">+44 (0)7582 913 406
        <svg class="contact-icon" viewBox="0 0 20 20" aria-hidden="true"><path fill="#fff" d="M5 2l3 4-2 2c1 2.5 3.5 5 6 6l2-2 4 3-2 3C9 18 2 11 2 4z"/></svg>
      </li>
      <li class="contact-item">sales@corvanemotion.co.uk
        <svg class="contact-icon" viewBox="0 0 20 20" aria-hidden="true"><rect x="3" y="5" width="14" height="10" fill="#fff"/><path d="M3 5l7 6 7-6" fill="none" stroke="var(--navy)" stroke-width="1.5"/></svg>
      </li>
      <li class="contact-item">Corvanemotion.co.uk
        <svg class="contact-icon" viewBox="0 0 20 20" aria-hidden="true"><circle cx="10" cy="10" r="8" fill="#fff"/><ellipse cx="10" cy="10" rx="3.5" ry="8" fill="none" stroke="var(--navy)" stroke-width="1.2"/><path d="M2 10h16" stroke="var(--navy)" stroke-width="1.2"/></svg>
      </li>
      <li class="contact-item">@motionLetterbin
        <svg class="contact-icon" viewBox="0 0 20 20" aria-hidden="true"><rect x="3" y="3" width="14" height="14" rx="2" fill="#fff"/></svg>
      </li>
      <li class="contact-item">Corvane Motion Limited
        <svg class="contact-icon" viewBox="0 0 20 20" aria-hidden="true"><rect x="3" y="3" width="14" height="14" rx="2" fill="#fff"/></svg>
      </li>
    </ul>
  </main>
</body>
</html>
```